New Business Card Design for Manufacturing

We are an engineering/manufacturing company that offers Advanced machining/assembly/engineering services, as well as innovative products for the heavy duty engine cooling markets.

We are looking to get a new business card designed that is clean and modern looking, but still fits the wide range of technical/skilled work we do.

- We hope to use this design as the base for other design work in new Presentations, web, and print work.

Industry/Entity Type

Engineering

Contact Information for Business Card

Our preferred color of blue is (RGB) 22/71/159 but can vary slightly from that color. Our content will be our Logo and full company name (Vantrell Forge Works, Inc.), company address, name, job title, phone number with extension, cell number, fax number, website, and email address on the cards.
We'd like the full company name next to the logo, but we are open to other interpretations of that layout.
Preferably, we would like the back side to be clean with just our logo, and the front to contain all of the contact information.

Colors
2f74b4
0355a3
85abd2

Requirements
Must have
• - Logo, company name, needed content - We are open to interpretation beyond that.
• - Standard size business card.
• - Horizontal orientation.
• - Enough space for lengthy names / job titles (for example, a job title could read "Directory of Human Resources" or "V.P. of Governmental Affairs"). We need this to look clean, whether the title be short (CEO) or long (as described above).

```html
<!DOCTYPE html>
<html lang="en">
<head>
<meta charset="utf-8">
<title>Vantrell Forge Works, Inc. — Business Card</title>
<link rel="stylesheet" href="https://fonts.googleapis.com/css2?family=Montserrat:wght@400;500;700;800&display=swap">
<style>
  :root {
    --brand-blue: #16479f;
    --blue-mid: #0355a3;
    --blue-soft: #2f74b4;
    --blue-pale: #85abd2;
    --card-black: #0a0a0b;
    --text-grey: #6c7178;
    --page: #e6e7e9;
    --white: #ffffff;
  }
  * { box-sizing: border-box; margin: 0; padding: 0; }
  html, body { width: 1200px; height: 900px; overflow: hidden; }
  body {
    background: var(--page);
    font-family: "Montserrat", Arial, sans-serif;
    position: relative;
  }
  .card {
    position: absolute;
    width: 630px;
    height: 360px;
    overflow: hidden;
    box-shadow: 0 10px 30px rgba(0,0,0,0.18);
  }

  /* Back side */
  .card-back { left: 60px; top: 45px; background: var(--card-black); }
  .card-back .pattern-area {
    position: absolute; left: 0; top: 0; width: 60%; height: 100%;
    background: linear-gradient(135deg, #111214 0%, #0a0a0b 70%);
  }
  .card-back .network-area {
    position: absolute; right: -60px; top: -40px; width: 330px; height: 330px;
    border-radius: 50%;
    background: radial-gradient(circle, #15181d 0%, #0e1013 60%, #0a0a0b 100%);
  }
  .card-back .brand-panel {
    position: absolute; left: 0; bottom: 0; width: 69%; height: 44%;
    background: var(--brand-blue);
    display: flex; align-items: center; gap: 16px;
    padding: 0 28px;
  }
  .brand-mark {
    width: 30px; height: 30px; flex: none;
    background: var(--white);
  }
  .card-back .brand-name {
    color: var(--white); font-weight: 800; font-size: 25px;
    line-height: 1.1; text-transform: uppercase; letter-spacing: 0.3px;
  }

  /* Front side */
  .card-front { left: 510px; top: 495px; background: var(--white); }
  .card-front .logo-panel {
    position: absolute; left: 68px; top: 0; width: 250px; height: 150px;
    background: var(--brand-blue);
    display: flex; align-items: center; gap: 14px; padding: 0 22px;
  }
  .card-front .logo-panel .brand-mark { width: 24px; height: 24px; }
  .card-front .brand-name {
    color: var(--white); font-weight: 800; font-size: 20px;
    line-height: 1.12; text-transform: uppercase;
  }
  .rule-long {
    position: absolute; left: 318px; right: 0; top: 98px;
    height: 3px; background: var(--blue-mid);
  }
  .contact-block { position: absolute; left: 82px; top: 172px; }
  .person-name {
    color: var(--blue-mid); font-weight: 700; font-size: 19px;
    text-transform: uppercase; letter-spacing: 0.3px;
  }
  .person-title {
    color: var(--text-grey); font-size: 13px; font-weight: 400; margin-top: 2px;
  }
  .rule-short {
    width: 152px; height: 3px; background: var(--blue-pale); margin: 14px 0 10px;
  }
  .contact-list { list-style: none; }
  .contact-list li {
    display: flex; align-items: center; gap: 10px;
    color: var(--text-grey); font-size: 13.5px; height: 24px;
  }
  .contact-list svg { width: 16px; height: 16px; flex: none; }
  .address {
    position: absolute; right: 40px; top: 178px;
    color: var(--text-grey); font-size: 13.5px;
  }
</style>
</head>
<body>

<section class="card card-back" aria-label="Card back">
  <div class="pattern-area" role="img" aria-label="Faint pattern of machinery and engineering line icons"></div>
  <div class="network-area" role="img" aria-label="Faint globe made of connected network lines"></div>
  <div class="brand-panel">
    <span class="brand-mark"></span>
    <span class="brand-name">Vantrell Forge<br>Works, Inc.</span>
  </div>
</section>

<section class="card card-front" aria-label="Card front">
  <div class="logo-panel">
    <span class="brand-mark"></span>
    <span class="brand-name">Vantrell Forge<br>Works, Inc.</span>
  </div>
  <div class="rule-long"></div>

  <div class="contact-block">
    <p class="person-name">Marcus Lindell</p>
    <p class="person-title">V.P. of Governmental Affairs</p>
    <div class="rule-short"></div>
    <ul class="contact-list">
      <li>
        <svg viewBox="0 0 16 16" aria-hidden="true"><circle cx="8" cy="8" r="7" fill="none" stroke="#0355a3" stroke-width="1.3"/><path d="M5.4 4.6l1.3 1.4-.7 1c.5 1 1.2 1.8 2.3 2.4l1-.7 1.4 1.3-.8 1c-2.6-.5-4.8-2.8-5.3-5.4z" fill="#0355a3"/></svg>
        (864) 555-0142 x217
      </li>
      <li>
        <svg viewBox="0 0 16 16" aria-hidden="true"><circle cx="8" cy="8" r="7" fill="none" stroke="#0355a3" stroke-width="1.3"/><rect x="5.8" y="4" width="4.4" height="8" rx="0.8" fill="none" stroke="#0355a3" stroke-width="1.2"/></svg>
        540-555-0178
      </li>
      <li>
        <svg viewBox="0 0 16 16" aria-hidden="true"><circle cx="8" cy="8" r="8" fill="#0355a3"/><rect x="4.5" y="6.5" width="7" height="4" fill="#fff"/><rect x="5.8" y="4.5" width="4.4" height="2" fill="#fff"/></svg>
        540-555-0193
      </li>
      <li>
        <svg viewBox="0 0 16 16" aria-hidden="true"><circle cx="8" cy="8" r="7" fill="none" stroke="#0355a3" stroke-width="1.3"/><rect x="4.5" y="5.5" width="7" height="5" fill="none" stroke="#0355a3" stroke-width="1.1"/><path d="M4.5 5.5L8 8.4l3.5-2.9" fill="none" stroke="#0355a3" stroke-width="1.1"/></svg>
        m.lindell@vantrellforge.com
      </li>
    </ul>
  </div>

  <p class="address">418 Orwell Ln , Harlan KY 40831</p>
</section>

</body>
</html>
```